Gobal construction supply company needs new business card design

I need a business card design for my global supply company using an existing logo. i will be looking to print these on rounded corner cards with the black background version of my logo on the back. on the front white background, my logo again and my simple details.

```html
<!DOCTYPE html>
<html lang="en">
<head>
<meta charset="utf-8">
<title>Meridian Supply Works – Business Card</title>
<link rel="stylesheet" href="https://fonts.googleapis.com/css2?family=Roboto:wght@400;500;700&display=swap">
<style>
  :root {
    --stage: #2b2b2b;
    --card-white: #f7f7f7;
    --card-black: #1c1c1c;
    --ink: #111111;
    --ink-soft: #555555;
    --accent: #e00000;
    --paper: #ffffff;
  }
  * { margin: 0; padding: 0; box-sizing: border-box; }
  html, body {
    width: 1200px; height: 960px; overflow: hidden;
    background: var(--stage);
    font-family: "Roboto", Arial, sans-serif;
  }
  .canvas { position: relative; width: 1200px; height: 960px; }

  .card {
    position: absolute; width: 600px; height: 343px; border-radius: 24px;
  }
  .card--front { left: 186px; top: 113px; background: var(--card-white); }
  .card--back { left: 434px; top: 512px; background: var(--card-black); }

  /* front */
  .brand {
    position: absolute; left: 36px; top: 108px;
    font-weight: 700; font-size: 19px; line-height: 24px;
    letter-spacing: 0.2px; color: var(--ink);
  }

  .person { position: absolute; left: 36px; top: 196px; }
  .person__name { font-weight: 500; font-size: 22px; color: var(--ink); line-height: 22px; }
  .person__role { font-size: 15.5px; color: var(--accent); line-height: 20px; }
  .person__address { font-size: 14.5px; color: var(--ink-soft); line-height: 19px; margin-top: 2px; }

  .contacts { position: absolute; left: 335px; top: 198px; list-style: none; }
  .contacts li {
    display: flex; align-items: center; gap: 8px;
    font-size: 14.5px; color: var(--ink-soft); line-height: 19px;
  }
  .contacts svg { width: 14px; height: 14px; fill: var(--ink); flex: none; }

  .band { position: absolute; top: 289px; height: 27px; }
  .band--dark { left: 32px; width: 282px; background: var(--ink); }
  .band--accent {
    left: 318px; width: 253px; background: var(--accent);
    color: var(--paper); font-size: 14.5px; letter-spacing: 0.6px;
    display: flex; align-items: center; justify-content: center;
  }

  /* back */
  .back-brand {
    position: absolute; inset: 0;
    display: flex; align-items: center; justify-content: center;
    font-weight: 700; font-size: 58px; color: var(--card-white); letter-spacing: 1px;
  }
</style>
</head>
<body>
<main class="canvas">
  <section class="card card--front" aria-label="Card front">
    <p class="brand">MERIDIAN SUPPLY WORKS</p>

    <div class="person">
      <p class="person__name">DANIEL HART</p>
      <p class="person__role">CEO/FOUNDER</p>
      <p class="person__address">2140 Harbor View Road<br>Portland, Oregon 97201</p>
    </div>

    <ul class="contacts">
      <li>
        <svg viewBox="0 0 24 24"><path d="M6.6 10.8a15.1 15.1 0 0 0 6.6 6.6l2.2-2.2c.3-.3.7-.4 1-.2 1.1.4 2.3.6 3.6.6.6 0 1 .4 1 1V20c0 .6-.4 1-1 1C10.6 21 3 13.4 3 4c0-.6.4-1 1-1h3.5c.6 0 1 .4 1 1 0 1.3.2 2.5.6 3.6.1.3 0 .7-.2 1z"/></svg>
        503 218 4471
      </li>
      <li>
        <svg viewBox="0 0 24 24"><path d="M7 1h10a2 2 0 0 1 2 2v18a2 2 0 0 1-2 2H7a2 2 0 0 1-2-2V3a2 2 0 0 1 2-2zm0 3v15h10V4zm5 16.2a1 1 0 1 0 0 .1z"/></svg>
        503 772 0158
      </li>
      <li>
        <svg viewBox="0 0 24 24"><path d="M6 2h12v5H6zM3 8h18a2 2 0 0 1 2 2v7h-4v5H5v-5H1v-7a2 2 0 0 1 2-2zm4 8v4h10v-4z"/></svg>
        503 218 4490
      </li>
      <li>
        <svg viewBox="0 0 24 24"><path d="M2 5h20v14H2zm2 2v.5l8 5 8-5V7zm0 2.9V17h16V9.9l-8 5z"/></svg>
        daniel@meridiansupply.com
      </li>
    </ul>

    <div class="band band--dark"></div>
    <div class="band band--accent">www.meridiansupplyworks.com</div>
  </section>

  <section class="card card--back" aria-label="Card back">
    <p class="back-brand">MERIDIAN</p>
  </section>
</main>
</body>
</html>
```